New Website Announcement

We need a flyer to announce our new website to customers and prospective clients. The website will be launching soon, but I can provide a detailed outline in PDF form with copy and imagery to serve as inspiration for this design.

I would like a postcard size document that can be mailed in an envelope (no need for postcard style mailer info on 1 side)

About my company:

Verity Lane Studio is a new breed of marketing consulting agency built for the next frontier of consumer learning. Social interaction will be at the heart of great insights going forward – in how consumers engage with brands and in how organizations socialize what they learn to gain competitive advantage.
By fusing innovative insights techniques, technology and compelling graphic design-based reporting, we ensure results get noticed and make an impact.

contact info that can also be included:

Email: marek@veritylane-studio.net

Phone: 518-732-5164

Thanks

Attention all designers submitting a design for this project. Please keep in mind a few important details about this project.

1. Remember that the main objective of this postcard is to announce my new website.

2. Please be sure to read the brief for the copy I would like on each side. You can be creative in how it is displayed, but I need this key information somewhere. All other copy on the attached files is for your background only.

3. Please do not submit overly simple designs that just take the images I provided and overlay a text box with my copy. I could easily do this myself in PowerPoint in 5 minutes.

4. Remember that the design should be edgy and modern but needs to be professional and speak to a business audience.

Please submit any questions. Thank you for your submissions. 

Marek

Target Market(s)

senior level marketing and research clients at large companies and agencies

Industry/Entity Type

Marketing

Requirements
Must have
• Main message:

Need an engaging way to tell customers and prospective clients that we have a new website and that they should come visit us online to learn more about out services, check out case studies and read about our exciting partnerships.

COPY TO USE - UPDATED

Side 1:
(logo)
Introducing Verity Lane Studio

Let’s talk about taking research out of the dark ages.

Visit our newly launched website to learn how and get in touch.

www.veritylane-studio.net

Side 2
Logo
followed by tagline:
Consumer insights that get noticed.
A leading-edge marketing partnership that really works.

Additional text to use on Side 2:
How we can help...

Think of us as your go-to resource for identifying and incorporating the most innovative and exciting techniques into your research programs. We carefully curate and develop close partnerships with the best of the best - from online qualitative research and mobile ethnography to social media listening and fresh takes on concept testing, we can guide the way.

Plus, we believe that socializing consumer learning is just as critical as gathering it.By taking insights deliverables to the next level – through infographics, videos, magazines,interactive profiles and so much more – we are getting stakeholders excited to engage with research and inspired to take action because of it.
It’s a new way to look at insights from a new type of partner. And, it’s a new way to get the most from your research dollars.
Nice to have
• could incorporate our website main image of the lamp on white brick background which is attached, but not 100% mandatory.
Should not have
• - should not be too playful or young, but needs to be modern and design focused

- should not be cluttered or overly 'salesy'

- needs to be upscale and elegant / compelling and aligned with the look and feel of the website imagery (see attached)

```html
<!DOCTYPE html>
<html lang="en">
<head>
<meta charset="utf-8">
<title>Verity Lane Studio – How we can help</title>
<link rel="stylesheet" href="https://fonts.googleapis.com/css2?family=Fira+Sans+Condensed:wght@600;700&family=Mulish:wght@400&family=Kameron:wght@400&display=swap">
<style>
  :root {
    --page: #ffffff;
    --card: #ffffff;
    --ink: #1a1a1a;
    --brand-blue: #2f6fb8;
    --link-blue: #3a72b5;
    --band-dark: #050505;
    --band-sheen: #3a3a3a;
    --ring: #ffffff;
    --dot-light: #4a9be0;
    --dot-dark: #1a5fae;
  }
  * { box-sizing: border-box; margin: 0; padding: 0; }
  html, body {
    width: 1200px;
    height: 882px;
    overflow: hidden;
    background: var(--page);
  }
  .postcard {
    position: absolute;
    left: 32px;
    top: 32px;
    width: 1136px;
    height: 818px;
    background: var(--card);
    box-shadow: 0 0 14px rgba(0,0,0,0.55);
  }
  .brand-name {
    position: absolute;
    left: 125px;
    top: 118px;
    width: 260px;
    font-family: "Fira Sans Condensed", sans-serif;
    font-weight: 700;
    font-size: 44px;
    line-height: 52px;
    color: var(--brand-blue);
    text-transform: uppercase;
  }
  .tagline {
    position: absolute;
    left: 418px;
    top: 114px;
    font-family: "Fira Sans Condensed", sans-serif;
    font-weight: 700;
    font-size: 30px;
    line-height: 36px;
    color: var(--brand-blue);
    letter-spacing: -0.2px;
  }
  .section-band {
    position: absolute;
    left: 200px;
    top: 274px;
    width: 902px;
    height: 56px;
    background: linear-gradient(100deg, var(--band-dark) 0%, var(--band-dark) 68%, var(--band-sheen) 76%, var(--band-dark) 84%, var(--band-dark) 100%);
    box-shadow: 0 4px 8px rgba(0,0,0,0.35);
  }
  .section-title {
    position: absolute;
    left: 218px;
    top: 279px;
    font-family: "Fira Sans Condensed", sans-serif;
    font-weight: 600;
    font-size: 38px;
    line-height: 46px;
    color: #ffffff;
  }
  .section-marker {
    position: absolute;
    left: 111px;
    top: 257px;
    width: 92px;
    height: 92px;
  }
  .body-copy {
    position: absolute;
    left: 218px;
    top: 350px;
    width: 852px;
    font-family: "Mulish", sans-serif;
    font-weight: 400;
    font-size: 18px;
    line-height: 34px;
    color: var(--ink);
  }
  .contact {
    position: absolute;
    left: 218px;
    top: 710px;
    font-family: "Kameron", serif;
    font-size: 19px;
    line-height: 26px;
    color: var(--link-blue);
  }
</style>
</head>
<body>
  <main class="postcard">
  </main>

  <div class="brand-name">Verity Lane<br>Studio</div>

  <h2 class="tagline">Consumer insights that get noticed.<br>A leading-edge marketing partnership that really works</h2>

  <div class="section-band"></div>
  <svg class="section-marker" viewBox="0 0 92 92" aria-hidden="true">
    <defs>
      <linearGradient id="markerFill" x1="0" y1="0" x2="1" y2="1">
        <stop offset="0" stop-color="#4a9be0"/>
        <stop offset="1" stop-color="#1a5fae"/>
      </linearGradient>
    </defs>
    <circle cx="46" cy="46" r="44" fill="#ffffff" stroke="#d0d0d0" stroke-width="1"/>
    <circle cx="46" cy="46" r="35" fill="url(#markerFill)"/>
  </svg>
  <h1 class="section-title">How we can help...</h1>

  <div class="body-copy">
    <p>Think of us as your go-to resource for identifying and incorporating the most innovative and exciting techniques into your research programs. We carefully curate and develop close partnerships with the best of the best - from online qualitative research and mobile ethnogra&shy;phy to social media listening and fresh takes on concept testing, we can guide the way.</p>
    <p>Plus, we believe that socializing consumer learning is just as critical as gathering it. By taking insights deliverables to the next level – through infographics, videos, magazines, interactive profiles and so much more – we are getting stakeholders excited to engage with research and inspired to take action because of it.</p>
    <p>It’s a new way to look at insights from a new type of partner. And, it’s a new way to get the most from your research dollars.</p>
  </div>

  <address class="contact" style="font-style: normal;">
    Email: marek@veritylane-studio.net<br>
    Phone: 518-732-5164
  </address>
</body>
</html>
```